Pyschiatry Experts need Marketing Campaign

Ad(s) developed for print advertising sharing our purpose and services, highlighting our medical care providers. Must be welcoming and inviting while displaying a high level of professionalism expected from a physician's office.

Target Market(s)

Local community

Industry/Entity Type

Psychiatry (Healthcare)

Requirements
Must have
• Staff pictures, 'Medication Management Experts', 'Prompt Appointments', 'ADD/ADHD, Bipolar Disorder, Depression, Anxiety, Schizophrenia, Grief Reaction and others' 'Virtual and In-Person Visits'
Nice to have
• Address: 412 E Marlowe Coeur d'Alene Phone (208)555-7193 website: BrightLoftCare.com Hours: Mon - Thur 7am - 6pm

```html
<!DOCTYPE html>
<html lang="en">
<head>
<meta charset="utf-8">
<title>Brightloft Care – Medication Management Experts</title>
<link rel="stylesheet" href="https://fonts.googleapis.com/css2?family=Poppins:wght@400;500;600;700;800&display=swap">
<style>
  :root{
    --teal:#0f8f7e;
    --deep:#0b5e4c;
    --lime:#a6df4e;
    --lime-soft:#c6ee8c;
    --ink:#1a1a1a;
    --paper:#ffffff;
    --backdrop:#ececec;
  }
  *{box-sizing:border-box;margin:0;padding:0}
  html,body{width:1200px;height:1200px;overflow:hidden;background:var(--backdrop)}
  body{font-family:"Poppins",sans-serif;color:var(--ink)}
  .flyer{position:absolute;left:150px;top:18px;width:899px;height:1164px;background:var(--paper);overflow:hidden}
  .abs{position:absolute}
  .brand{left:64px;top:44px;width:240px;text-align:center}
  .brand-mark{width:62px;height:62px;border-radius:50%;background:var(--teal);margin:0 auto 10px}
  .brand-name{font-weight:600;font-size:27px;line-height:1;color:var(--teal);letter-spacing:1px}
  .brand-sub{font-weight:600;font-size:15px;color:var(--teal);letter-spacing:3px;margin-top:6px}
  .headline{left:388px;top:39px;line-height:44px;font-size:52px;white-space:nowrap}
  .headline span{display:block;height:44px}
  .headline .light{font-weight:400;letter-spacing:-.5px;color:var(--ink)}
  .headline .bold{font-weight:800;letter-spacing:1.5px;color:var(--teal)}
  .services{left:388px;top:174px;font-weight:600;font-size:18.5px;line-height:23px;color:var(--ink);white-space:nowrap}
  .hero{left:0;top:180px;width:899px;height:520px}
  .providers-banner{left:372px;top:644px;width:470px;height:47px;background:var(--deep);color:#fff;font-weight:700;font-size:19.5px;display:flex;align-items:center;justify-content:center;white-space:nowrap}
  .providers-banner span{color:var(--lime)}
  .expertise-title{left:64px;top:702px;font-size:23px;font-weight:400;letter-spacing:1.5px}
  .expertise-title b{color:var(--teal);font-weight:700}
  .expertise-list{left:64px;top:746px;list-style:none;font-weight:600;font-size:18.5px}
  .expertise-list li{display:flex;align-items:center;height:32.3px}
  .expertise-list svg{width:18px;height:18px;margin:0 14px 0 1px;flex:none}
  .expertise-list .more{font-weight:400;padding-left:33px}
  .provider-photo{width:126px;height:126px;border-radius:50%;background:var(--lime-soft);padding:8px}
  .provider-photo div{width:100%;height:100%;border-radius:50%;border:3px solid #fff;background:radial-gradient(circle at 50% 40%,#8a9191,#3c4645)}
  .provider-name{font-weight:700;font-size:22px;line-height:27px;color:var(--deep);white-space:nowrap}
  .provider-cred{font-size:13.5px;margin-top:1px;white-space:nowrap}
  .cta-bar{left:77px;top:985px;width:745px;height:34px;border-radius:17px;background:var(--deep);display:flex;align-items:center;color:#fff;font-weight:700;font-size:20px;letter-spacing:1.5px;white-space:nowrap}
  .cta-bar .prompt{background:var(--lime);color:var(--ink);height:100%;width:328px;flex:none;border-radius:17px;display:flex;align-items:center;padding-left:18px}
  .cta-bar .visits{padding-left:16px}
  .contact{display:flex;align-items:center;white-space:nowrap}
  .contact .icon{width:30px;height:30px;border-radius:50%;background:var(--teal);display:flex;align-items:center;justify-content:center;margin-right:10px;flex:none}
  .phone{left:64px;top:1036px;font-weight:500;font-size:31px;letter-spacing:.5px}
  .address{left:64px;top:1078px;font-weight:500;font-size:20px}
  .web{left:475px;top:1039px;font-weight:500;font-size:20px;letter-spacing:2.5px}
  .hours{left:475px;top:1078px;font-weight:500;font-size:20px}
  .hours b{color:var(--teal);font-weight:600}
  .hours i{font-style:normal;color:#999;margin:0 4px}
</style>
</head>
<body>
<main class="flyer">

  <svg class="abs hero" viewBox="0 180 899 520">
    <defs>
      <linearGradient id="photoTone" x1="0" y1="0" x2="1" y2="1">
        <stop offset="0" stop-color="#dfe6ea"/>
        <stop offset=".5" stop-color="#a9b0b8"/>
        <stop offset="1" stop-color="#e9eef0"/>
      </linearGradient>
    </defs>
    <path d="M298,196 A243,243 0 0 0 298,682 L298,655 A216,216 0 0 1 298,223 Z" fill="var(--deep)"/>
    <path d="M298,215 A224,224 0 0 0 298,663" fill="none" stroke="#fff" stroke-width="2"/>
    <path d="M303,215 A224,224 0 0 1 478,300 L454,318 A194,194 0 0 0 303,245 Z" fill="var(--lime)"/>
    <g role="img" aria-label="Photo of the cheerful care team gathered around a meeting table">
      <path d="M150,306 H782 A60,60 0 0 1 842,366 V611 H190 A40,40 0 0 1 150,571 Z" fill="url(#photoTone)" stroke="var(--deep)" stroke-width="1.5"/>
    </g>
  </svg>

  <div class="abs brand">
    <div class="brand-mark"></div>
    <div class="brand-name">BRIGHTLOFT</div>
    <div class="brand-sub">CARE</div>
  </div>

  <h1 class="abs headline">
    <span class="light">MEDICATION</span>
    <span class="bold">MANAGEMENT</span>
    <span class="bold">EXPERTS</span>
  </h1>
  <p class="abs services">Mental Health and Psychiatry Services<br>Migraine and Neurospasticity Intervention</p>

  <div class="abs providers-banner"><span>MEET OUR&nbsp;</span>MENTAL HEALTH PROVIDERS</div>

  <h2 class="abs expertise-title">WE <b>EXPERTISE IN</b></h2>
  <ul class="abs expertise-list">
    <li><svg viewBox="0 0 18 18"><circle cx="9" cy="9" r="9" fill="var(--teal)"/><path d="M5 9.3l2.7 2.6L13 6.5" fill="none" stroke="#fff" stroke-width="2"/></svg>ADD/ADHD</li>
    <li><svg viewBox="0 0 18 18"><circle cx="9" cy="9" r="9" fill="var(--teal)"/><path d="M5 9.3l2.7 2.6L13 6.5" fill="none" stroke="#fff" stroke-width="2"/></svg>Bipolar Disorder</li>
    <li><svg viewBox="0 0 18 18"><circle cx="9" cy="9" r="9" fill="var(--teal)"/><path d="M5 9.3l2.7 2.6L13 6.5" fill="none" stroke="#fff" stroke-width="2"/></svg>Depression</li>
    <li><svg viewBox="0 0 18 18"><circle cx="9" cy="9" r="9" fill="var(--teal)"/><path d="M5 9.3l2.7 2.6L13 6.5" fill="none" stroke="#fff" stroke-width="2"/></svg>Anxiety</li>
    <li><svg viewBox="0 0 18 18"><circle cx="9" cy="9" r="9" fill="var(--teal)"/><path d="M5 9.3l2.7 2.6L13 6.5" fill="none" stroke="#fff" stroke-width="2"/></svg>Schizophrenia</li>
    <li><svg viewBox="0 0 18 18"><circle cx="9" cy="9" r="9" fill="var(--teal)"/><path d="M5 9.3l2.7 2.6L13 6.5" fill="none" stroke="#fff" stroke-width="2"/></svg>Grief Reaction</li>
    <li class="more">and others</li>
  </ul>

  <div class="abs provider-photo" style="left:349px;top:703px" role="img" aria-label="Portrait of Owen Marsh"><div></div></div>
  <div class="abs" style="left:486px;top:733px"><div class="provider-name">OWEN<br>MARSH</div><div class="provider-cred">PMHNP-BC</div></div>

  <div class="abs provider-photo" style="left:604px;top:703px" role="img" aria-label="Portrait of Dale Pruett"><div></div></div>
  <div class="abs" style="left:736px;top:733px"><div class="provider-name">DALE<br>PRUETT</div><div class="provider-cred">PMHNP-BC</div></div>

  <div class="abs provider-photo" style="left:349px;top:840px" role="img" aria-label="Portrait of Carla Whitby"><div></div></div>
  <div class="abs" style="left:486px;top:872px"><div class="provider-name">CARLA<br>WHITBY</div><div class="provider-cred">PMHNP-BC</div></div>

  <div class="abs provider-photo" style="left:604px;top:840px" role="img" aria-label="Portrait of Ruth Danner"><div></div></div>
  <div class="abs" style="left:736px;top:872px"><div class="provider-name">RUTH<br>DANNER</div><div class="provider-cred">PMHNP-BC, DNP</div></div>

  <div class="abs cta-bar">
    <div class="prompt">PROMPT APPOINTMENTS</div>
    <div class="visits">VIRTUAL AND IN-PERSON VISITS</div>
  </div>

  <div class="abs contact phone">
    <span class="icon"><svg width="16" height="16" viewBox="0 0 24 24"><path d="M6.6 10.8a15 15 0 0 0 6.6 6.6l2.2-2.2c.3-.3.7-.4 1-.2 1.1.4 2.3.6 3.6.6.6 0 1 .4 1 1V20c0 .6-.4 1-1 1A17 17 0 0 1 3 4c0-.6.4-1 1-1h3.5c.6 0 1 .4 1 1 0 1.3.2 2.5.6 3.6.1.3 0 .7-.2 1z" fill="#fff"/></svg></span>(208)555-7193
  </div>
  <div class="abs contact address">
    <span class="icon"><svg width="14" height="18" viewBox="0 0 14 18"><path d="M7 0a7 7 0 0 0-7 7c0 5 7 11 7 11s7-6 7-11a7 7 0 0 0-7-7zm0 9.5A2.5 2.5 0 1 1 7 4.5a2.5 2.5 0 0 1 0 5z" fill="#fff"/></svg></span>412 E Marlowe Coeur d'Alene
  </div>
  <div class="abs contact web">
    <span class="icon"><svg width="18" height="18" viewBox="0 0 20 20" fill="none" stroke="#fff" stroke-width="1.5"><circle cx="10" cy="10" r="8"/><ellipse cx="10" cy="10" rx="3.5" ry="8"/><path d="M2 10h16M3.5 6h13M3.5 14h13"/></svg></span>www.brightloftcare.com
  </div>
  <div class="abs contact hours">
    <span class="icon"><svg width="16" height="16" viewBox="0 0 20 20" fill="none" stroke="#fff" stroke-width="1.6"><rect x="2" y="4" width="16" height="14" rx="2"/><path d="M2 8h16M6 2v4M14 2v4"/></svg></span><b>Monday - Thursday</b><i>|</i>7am - 6pm
  </div>

</main>
</body>
</html>
```